High-end construction company needs a business card design

We need a modern looking business card that draws people in, is memorable and looks so good people will want to sick it on their fridges.
On the first side what is needed are:
Logo
My name - Tomasz Brelwik
Title - Managing Director
Website - www.varkelt.co.uk
Email - tomasz@varkelt.co.uk
Telephone - 020 5194 6281
Mobile - 07845139072
On the back side was is needed is a list of all the services we provide:
-Kitchen Renovations
-Bathroom Renovations
-House Renovations
-Garage Conversions
-Extensions
-Loft Conversions
-Conservatories
-Carpentry
-Tiling
-Electrical
-Plumbing & Heating
-Bricklaying
-Landscaping
-Decorating
-Plastering
We would like the colours to be the same shades as on the logo with grey or black for the words.
Target Market(s)
Anyone who needs building work done
Contact Information for Business Card
This business card is for a construction company which strives to deliver excellent service and quality.
The look and feel of the card should represent this.
Requirements
Must have
- On the first side what is needed are:
Logo
My name - Tomasz Brelwik
Title - Managing Director
Website - www.varkelt.co.uk
Email - tomasz@varkelt.co.uk
Telephone - 020 5194 6281
Mobile - 07845139072
Nice to have
- Cool looking features

```html
<!DOCTYPE html>
<html lang="en">
<head>
<meta charset="utf-8">
<title>Varkelt Construction – Business Card</title>
<link href="https://fonts.googleapis.com/css2?family=Arimo:wght@400;700&family=Open+Sans:wght@400;600&display=swap" rel="stylesheet">
<style>
  :root {
    --canvas: #9a9a9a;
    --card-dark: #333234;
    --card-dark-soft: #3a393b;
    --brand-green: #6fbe44;
    --brand-green-deep: #4f8f2e;
    --band-light: #b9b9bb;
    --band-mid: #8e8e90;
    --ink: #333333;
    --white: #ffffff;
  }
  html, body {
    margin: 0;
    width: 1200px;
    height: 1200px;
    overflow: hidden;
    background: var(--canvas);
  }
  .stage {
    position: relative;
    width: 1200px;
    height: 1200px;
  }
  .card {
    position: absolute;
    left: 250px;
    width: 700px;
    height: 400px;
    border-radius: 22px;
    overflow: hidden;
    background: var(--card-dark);
  }
  .card--front { top: 190px; }
  .card--back { top: 610px; }
  .card__art {
    position: absolute;
    inset: 0;
  }
  .brand-name {
    position: absolute;
    left: 46px;
    top: 92px;
    margin: 0;
    font-family: "Arimo", Arial, sans-serif;
    font-weight: 700;
    font-size: 46px;
    letter-spacing: 1px;
    color: var(--brand-green);
  }
  .holder {
    position: absolute;
    left: 475px;
    top: 60px;
  }
  .holder__name {
    margin: 0;
    font-family: "Arimo", Arial, sans-serif;
    font-weight: 700;
    font-size: 26px;
    color: var(--white);
  }
  .holder__title {
    margin: 10px 0 0;
    font-family: "Arimo", Arial, sans-serif;
    font-size: 12px;
    color: var(--ink);
  }
  .contacts {
    position: absolute;
    left: 280px;
    top: 242px;
    margin: 0;
    padding: 0;
    list-style: none;
  }
  .contacts__item {
    display: flex;
    align-items: center;
    height: 32px;
    font-family: "Arimo", Arial, sans-serif;
    font-weight: 700;
    font-size: 17px;
    color: var(--ink);
  }
  .contacts__icon {
    width: 22px;
    height: 22px;
    margin-right: 25px;
    flex: none;
  }
  .pattern-field {
    position: absolute;
    inset: 0;
    background: linear-gradient(160deg, var(--card-dark-soft), var(--card-dark) 70%);
  }
  .services {
    position: absolute;
    left: 0;
    right: 0;
    top: 232px;
    text-align: center;
    font-family: "Open Sans", Arial, sans-serif;
    color: var(--white);
  }
  .services__heading {
    margin: 0 0 4px;
    font-size: 15px;
    font-weight: 600;
    color: var(--brand-green);
    text-decoration: underline;
  }
  .services__line {
    margin: 0;
    font-size: 14.5px;
    line-height: 20.5px;
  }
</style>
</head>
<body>
<main class="stage">

  <section class="card card--front" aria-label="Business card front">
    <svg class="card__art" viewBox="0 0 700 400" width="700" height="400" aria-hidden="true">
      <path d="M470,0 C300,55 175,210 190,400 L700,400 L700,0 Z" fill="var(--band-mid)"/>
      <path d="M460,0 C305,60 192,210 207,400 L700,400 L700,0 Z" fill="var(--band-light)"/>
      <path d="M452,0 C310,62 208,210 224,400 L700,400 L700,0 Z" fill="var(--brand-green)"/>
    </svg>

    <p class="brand-name">VARKELT</p>

    <div class="holder">
      <h1 class="holder__name">Tomasz Brelwik</h1>
      <p class="holder__title">Managing Director</p>
    </div>

    <ul class="contacts">
      <li class="contacts__item">
        <svg class="contacts__icon" viewBox="0 0 22 22" aria-hidden="true">
          <circle cx="11" cy="11" r="10" fill="var(--brand-green-deep)" stroke="#ffffff" stroke-width="1"/>
          <path d="M5,9 Q11,4 17,9 L15.5,11 L13.5,10 L13.5,8.5 Q11,7.6 8.5,8.5 L8.5,10 L6.5,11 Z" fill="#ffffff"/>
          <rect x="7" y="12" width="8" height="4.5" rx="1" fill="#ffffff"/>
        </svg>
        020 5194 6281
      </li>
      <li class="contacts__item">
        <svg class="contacts__icon" viewBox="0 0 22 22" aria-hidden="true">
          <circle cx="11" cy="11" r="10" fill="var(--brand-green-deep)" stroke="#ffffff" stroke-width="1"/>
          <path d="M7,5.5 L9,5 L10.2,8 L8.8,9.2 Q9.8,11.8 12.8,13.2 L14,11.8 L17,13 L16.5,15 Q15.5,16.5 13.5,16 Q7.5,14 6,8 Q5.7,6.3 7,5.5 Z" fill="#ffffff"/>
        </svg>
        07845139072
      </li>
      <li class="contacts__item">
        <svg class="contacts__icon" viewBox="0 0 22 22" aria-hidden="true">
          <circle cx="11" cy="11" r="10" fill="var(--brand-green-deep)" stroke="#ffffff" stroke-width="1"/>
          <rect x="5.5" y="7.5" width="11" height="7.5" fill="#ffffff"/>
          <path d="M5.5,7.5 L11,11.8 L16.5,7.5" fill="none" stroke="var(--brand-green-deep)" stroke-width="1"/>
        </svg>
        tomasz@varkelt.co.uk
      </li>
      <li class="contacts__item">
        <svg class="contacts__icon" viewBox="0 0 22 22" aria-hidden="true">
          <circle cx="11" cy="11" r="10" fill="var(--brand-green-deep)" stroke="#ffffff" stroke-width="1"/>
          <g fill="none" stroke="#ffffff" stroke-width="1">
            <circle cx="11" cy="11" r="6"/>
            <ellipse cx="11" cy="11" rx="2.6" ry="6"/>
            <line x1="5" y1="11" x2="17" y2="11"/>
            <line x1="11" y1="5" x2="11" y2="17"/>
          </g>
        </svg>
        www.varkelt.co.uk
      </li>
    </ul>
  </section>

  <section class="card card--back" aria-label="Business card back">
    <div class="pattern-field" role="img" aria-label="Faint diagonal repeat of the company name across the card background"></div>
    <div class="services">
      <h2 class="services__heading">Services</h2>
      <p class="services__line">• Kitchen Renovations • Bathroom Renovations • House Renovations</p>
      <p class="services__line">• Garage Conversions &nbsp;• Extensions • Loft Conversions</p>
      <p class="services__line">• Conservatories • Carpentry • Tiling • Electrical • Plumbing &amp; Heating</p>
      <p class="services__line">• Bricklaying • Landscaping • Decorating • Plastering</p>
    </div>
  </section>

</main>
</body>
</html>
```